Italian restaurant needs new site

Need to make our website better.

Must have reservation module

Must be able to sell wine tasting tours and wine pairing tours and intégrate with dunmo desk

Blog

Social media

Wandervane ranking and last review.
Updates

Number of Pages Required

1 page

Font styles to use
Serif

Requirements
Must have
• Reservation module
• Marketplace to buy wine pairings and gift certificates
• Wandervane review
• Kindlepost posts
• All info from old site

```html
<!DOCTYPE html>
<html lang="en">
<head>
<meta charset="utf-8">
<title>Corvina Bistro – Italian restaurant in Cabo San Lucas</title>
<link href="https://fonts.googleapis.com/css2?family=Special+Elite&family=Raleway:wght@400;600;700&display=swap" rel="stylesheet">
<style>
:root{
  --rust:#b4620f;
  --amber:#c9821d;
  --wine:#8a1c1f;
  --ink:#1e1e1e;
  --text:#5b5b5b;
  --mute:#9a9a9a;
  --line:#e2e2e2;
  --paper:#ffffff;
  --fog:#f1f1f1;
  --green:#34a853;
  --sky:#1e9fd8;
}
*{box-sizing:border-box;margin:0;padding:0}
html,body{width:1200px;height:4000px;overflow:hidden}
body{position:relative;background:var(--paper);font-family:"Raleway",sans-serif;color:var(--text);font-size:13px}
.display{font-family:"Special Elite",serif;color:var(--ink);letter-spacing:2px;font-weight:400}
.abs{position:absolute}
.btn{display:inline-flex;align-items:center;justify-content:center;border-radius:30px;font-weight:700;font-size:13px;text-transform:uppercase;letter-spacing:.5px}

/* header */
.site-header{left:0;top:0;width:1200px;height:120px;background:var(--paper);border-top:5px solid var(--wine);z-index:5}
.brand{left:100px;top:0;width:220px;height:190px;border-radius:0 0 110px 110px;background:var(--paper);z-index:6;display:flex;flex-direction:column;align-items:center;justify-content:center;padding-top:10px}
.brand-name{font-family:"Raleway",sans-serif;font-weight:700;color:var(--wine);font-size:30px;letter-spacing:1px}
.brand-sub{font-size:11px;color:var(--wine);letter-spacing:1px;margin-top:4px}
.nav{left:433px;top:52px;display:flex;gap:40px;font-size:13px;font-weight:600;color:var(--ink);z-index:6}
.nav-cta{left:714px;top:38px;width:160px;height:46px;background:var(--rust);color:#fff;z-index:6}
.call{left:895px;top:42px;display:flex;align-items:center;gap:12px;font-size:13px;font-weight:700;color:var(--wine);z-index:6}
.call-icon{width:38px;height:38px;border:1px solid var(--line);border-radius:50%;display:flex;align-items:center;justify-content:center}

/* hero */
.hero{left:0;top:120px;width:1200px;height:560px}
.hero-photo{position:absolute;inset:0;background:radial-gradient(ellipse at 55% 45%,#8a6d52 0%,#4d3a2c 45%,#23180f 100%)}
.hero-title{left:0;top:290px;width:1200px;text-align:center;font-size:72px;color:#fff;z-index:2}
.hero-sub{left:0;top:392px;width:1200px;text-align:center;font-family:"Special Elite",serif;font-size:22px;color:#fff;z-index:2}
.hero-btn{left:515px;top:468px;width:170px;height:46px;border:2px solid #fff;color:#fff;text-transform:none;font-size:15px;font-weight:600;z-index:2}
.dots{left:0;top:612px;width:1200px;display:flex;justify-content:center;gap:14px;z-index:3}
.dots span{width:11px;height:11px;border-radius:50%;border:2px solid #fff}
.dots span.on{background:#fff}
.hero-curve{left:0;top:560px;z-index:2}

/* tours */
.tours-title{left:99px;top:770px;font-size:36px}
.tours-copy{left:99px;top:825px;width:520px;font-size:12.5px;line-height:24px}
.tours-btn{left:99px;top:1050px;width:150px;height:46px;background:var(--rust);color:#fff}
.tours-photo-back{left:660px;top:775px;width:440px;height:310px;background:#e8e8e8;transform:rotate(4deg);box-shadow:0 4px 12px rgba(0,0,0,.2)}
.tours-photo{left:652px;top:782px;width:440px;height:300px;border:8px solid #fff;transform:rotate(-4deg);box-shadow:0 4px 14px rgba(0,0,0,.3);background:linear-gradient(135deg,#7a8c4a 0%,#b8a780 45%,#6e4d36 100%)}

/* blog */
.blog{left:0;top:1195px;width:1200px;height:805px;background:linear-gradient(135deg,#f3f3f3,#e9e9e9 50%,#f4f4f4)}
.section-title{left:0;width:1200px;text-align:center;font-size:36px}
.blog-grid{left:99px;top:1363px;width:1002px;height:554px;display:grid;grid-template-columns:repeat(3,1fr);grid-template-rows:repeat(2,1fr);box-shadow:0 4px 18px rgba(0,0,0,.12)}
.post-photo{position:relative}
.post-photo.warm{background:linear-gradient(140deg,#f2b25a,#b55a16 60%,#3c2110)}
.post-photo.toast{background:linear-gradient(140deg,#4a3020,#a0623a 55%,#2a1a10)}
.post-photo.cheers{background:linear-gradient(140deg,#b8b4ac,#8a6a50 50%,#4b2a20)}
.date{position:absolute;bottom:0;width:90px;height:84px;color:#fff;font-weight:700;font-size:20px;display:flex;flex-direction:column}
.date .m{background:var(--rust);height:42px;display:flex;align-items:center;padding-left:10px}
.date .y{height:42px;display:flex;align-items:center;padding-left:10px;background:#fff;color:var(--ink)}
.date.left{left:0}
.date.right{right:0}
.date.right .m,.date.right .y{justify-content:flex-end;padding-right:10px}
.post-text{background:#fff;padding:40px 32px 0}
.post-text h3{font-size:13px;font-weight:700;color:var(--ink);line-height:22px;text-transform:uppercase}
.post-meta{font-size:11px;color:var(--rust);margin:12px 0 10px;display:flex;gap:14px}
.post-text p{font-size:12px;line-height:21px}
.post-more{display:block;margin-top:14px;font-size:12px;font-weight:700;color:var(--rust)}

/* reviews */
.review{top:2187px;width:328px;height:124px;border:1px solid var(--line);border-radius:4px;background:#fff;padding:18px 22px}
.review-head{display:flex;align-items:center;justify-content:space-between}
.review-brand{display:flex;align-items:center;gap:8px;font-weight:700;font-size:17px;color:var(--ink)}
.review-brand i{width:20px;height:20px;border-radius:50%;background:var(--ink)}
.review-count{font-size:11px;color:var(--green)}
.review p{font-size:11.5px;line-height:19px;margin-top:14px}
.review-foot{width:328px;text-align:center;top:2352px}
.avatar{width:80px;height:80px;border-radius:50%;margin:0 auto;background:linear-gradient(135deg,#d9c3ae,#8c7767);border:3px solid #fff;box-shadow:0 0 0 1px var(--line)}
.reviewer{font-size:12px;color:var(--rust);margin-top:18px}
.stars{display:flex;justify-content:center;gap:3px;margin-top:10px}
.stars span{width:14px;height:14px;border-radius:50%;background:var(--green);border:2px solid #fff;box-shadow:0 0 0 1px var(--green)}
.arrow{top:2272px;font-size:26px;color:var(--ink)}

/* reservations */
.reserve{left:0;top:2592px;width:1200px;height:848px;background:linear-gradient(135deg,#c98a2a 0%,#b8701a 50%,#a85e14 100%)}
.reserve-title{top:2652px;color:#fff}
.reserve-copy{left:300px;top:2725px;width:600px;text-align:center;color:#fff;font-size:12.5px;line-height:22px}
.form{left:181px;top:2870px;width:835px;display:grid;grid-template-columns:repeat(3,1fr);column-gap:16px;row-gap:22px}
.field label{display:block;color:#fff;font-size:12px;margin-bottom:8px}
.field .input{height:42px;border:1px solid rgba(255,255,255,.55);background:rgba(255,255,255,.08)}
.field.wide{grid-column:1/4}
.field.wide .input{height:118px}
.reserve-btn{grid-column:1/4;height:48px;background:var(--wine);color:#fff;display:flex;align-items:center;justify-content:center;font-weight:700;font-size:13px;letter-spacing:1px;margin-top:4px}

/* contact */
.contact-title{left:99px;top:3525px;font-size:28px}
.contact-list{left:99px;top:3590px;width:240px}
.contact-item{display:flex;align-items:center;gap:16px;margin-bottom:22px;font-size:11.5px;line-height:18px}
.contact-item .ic{flex:none;width:44px;height:44px;border-radius:50%;border:1px solid var(--line);display:flex;align-items:center;justify-content:center}
.hours{left:99px;top:3808px;font-family:"Special Elite",serif;color:var(--wine);font-size:15px;letter-spacing:1px}
.tweets{left:373px;top:3539px;width:328px;height:294px;border:1px solid var(--line);background:#fff}
.tweets-head{height:44px;background:var(--sky);color:#fff;font-weight:700;font-size:15px;display:flex;align-items:center;justify-content:space-between;padding:0 18px}
.tweet{display:flex;gap:16px;padding:18px 18px;border-bottom:1px solid var(--line)}
.tweet .bird{flex:none;width:44px;height:44px;border-radius:50%;background:var(--sky)}
.tweet-body{font-size:11px;line-height:18px}
.tweet-body b{color:var(--wine);font-weight:600}
.tweet-date{color:var(--rust);font-size:10.5px}
.map{left:744px;top:3539px;width:357px;height:310px;background:linear-gradient(135deg,#ece9e2,#dcdcd4 50%,#e9e6de)}
.map-card{left:782px;top:3740px;width:150px;padding:10px 12px;background:#fff;font-size:11px;line-height:16px;box-shadow:0 1px 4px rgba(0,0,0,.2)}

/* footer */
.footer-line{left:99px;top:3926px;width:1002px;height:2px;background:var(--wine)}
.socials{left:99px;top:3950px;display:flex;gap:6px}
.socials span{width:26px;height:26px;border-radius:50%;border:1px solid var(--sky)}
.copyright{right:99px;top:3956px;font-size:11px;color:var(--text)}
</style>
</head>
<body>

<header class="site-header abs"></header>
<div class="brand abs">
  <div class="brand-name">Corvina</div>
  <div class="brand-sub">ITALIAN CUISINE &amp; WINE BAR</div>
</div>
<nav class="nav abs"><span>HOME</span><span>MENU</span><span>RESERVATIONS</span></nav>
<div class="nav-cta btn abs">Contact Us</div>
<div class="call abs">
  <span class="call-icon"><svg width="16" height="16" viewBox="0 0 24 24"><path fill="#8a1c1f" d="M6.6 10.8a15 15 0 0 0 6.6 6.6l2.2-2.2c.3-.3.7-.4 1-.2 1.1.4 2.3.6 3.6.6.6 0 1 .4 1 1V20c0 .6-.4 1-1 1A17 17 0 0 1 3 4c0-.6.4-1 1-1h3.5c.6 0 1 .4 1 1 0 1.3.2 2.5.6 3.6.1.3 0 .7-.2 1z"/></svg></span>
  <span>CALL US NOW ! 555 0142</span>
</div>

<section class="hero abs">
  <div class="hero-photo" role="img" aria-label="Glass of red wine on a restaurant table at dusk"></div>
</section>
<h1 class="hero-title display abs">CORVINA BISTRO</h1>
<p class="hero-sub abs">Italian restaurant in Cabo San Lucas</p>
<div class="hero-btn btn abs">Read more</div>
<div class="dots abs"><span class="on"></span><span></span><span></span><span></span><span></span></div>
<svg class="hero-curve abs" width="1200" height="130" viewBox="0 0 1200 130">
  <path d="M0 0 Q600 220 1200 0 L1200 130 L0 130 Z" fill="#fff"/>
  <path d="M0 0 Q600 220 1200 0" fill="none" stroke="#b4620f" stroke-width="6"/>
</svg>

<h2 class="tours-title display abs">WINE TASTING TOURS</h2>
<p class="tours-copy abs">Corvina Bistro sits in the heart of downtown, across from Plaza Marisol, just two short blocks up from Palmera Resort and the Cabo marina. It is a place with honest Southern Italian and Mediterranean cooking and a European touch. Sure to please your classic favorites or satisfy even the most distinctive palate, we offer a variety of homemade, fresh-cooked dishes drawn from generations-old family recipes, paired with an extensive upscale selection of national and international wines and fun Italian-inspired cocktails.</p>
<div class="tours-btn btn abs">Read more</div>
<div class="tours-photo-back abs"></div>
<div class="tours-photo abs" role="img" aria-label="Friends raising wine glasses on a vineyard tour"></div>

<section class="blog abs"></section>
<h2 class="section-title display abs" style="top:1272px">LATEST BLOG POSTS</h2>
<div class="blog-grid abs">
  <div class="post-photo warm" role="img" aria-label="Guests toasting at a sunlit bar">
    <div class="date left"><span class="m">Mar</span><span class="y">2017</span></div>
  </div>
  <article class="post-text">
    <h3>Quis nostrud exercitation ullam&shy;co laboris nisi ut aliquip</h3>
    <div class="post-meta"><span>By Admin</span><span>4 Comments</span></div>
    <p>Lorem ipsum dolor sit amet, consectetur adipisicing elit, sed do eiusmod tempor incididunt ut labore et dolore magna aliqua.</p>
    <span class="post-more">Read more »</span>
  </article>
  <div class="post-photo toast" role="img" aria-label="Friends clinking wine glasses at dinner">
    <div class="date right"><span class="m">Mar</span><span class="y">2017</span></div>
  </div>
  <article class="post-text">
    <h3>Quis nostrud exercitation ullam&shy;co laboris nisi ut aliquip</h3>
    <div class="post-meta"><span>By Admin</span><span>4 Comments</span></div>
    <p>Lorem ipsum dolor sit amet, consectetur adipisicing elit, sed do eiusmod tempor incididunt ut labore et dolore magna aliqua.</p>
    <span class="post-more">Read more »</span>
  </article>
  <div class="post-photo cheers" role="img" aria-label="Couple toasting with red wine">
    <div class="date left"><span class="m">Mar</span><span class="y">2017</span></div>
  </div>
  <article class="post-text">
    <h3>Quis nostrud exercitation ullam&shy;co laboris nisi ut aliquip</h3>
    <div class="post-meta"><span>By Admin</span><span>4 Comments</span></div>
    <p>Lorem ipsum dolor sit amet, consectetur adipisicing elit, sed do eiusmod tempor incididunt ut labore et dolore magna aliqua.</p>
    <span class="post-more">Read more »</span>
  </article>
</div>

<h2 class="section-title display abs" style="top:2095px">CUSTOMER REVIEWS</h2>
<div class="arrow abs" style="left:58px">‹</div>
<div class="arrow abs" style="left:1128px">›</div>

<div class="review abs" style="left:99px">
  <div class="review-head"><span class="review-brand"><i></i>Wandervane</span><span class="review-count">1,086 reviews</span></div>
  <p>It is a long established fact that a reader will be distracted by the readable content of a page.</p>
</div>
<div class="review abs" style="left:436px">
  <div class="review-head"><span class="review-brand"><i></i>Wandervane</span><span class="review-count">1,086 reviews</span></div>
  <p>It is a long established fact that a reader will be distracted by the readable content of a page.</p>
</div>
<div class="review abs" style="left:773px">
  <div class="review-head"><span class="review-brand"><i></i>Wandervane</span><span class="review-count">1,086 reviews</span></div>
  <p>It is a long established fact that a reader will be distracted by the readable content of a page.</p>
</div>
<div class="review-foot abs" style="left:99px"><div class="avatar" role="img" aria-label="Reviewer portrait"></div><div class="reviewer">Leo Marsh, Valued Client</div><div class="stars"><span></span><span></span><span></span><span></span><span></span></div></div>
<div class="review-foot abs" style="left:436px"><div class="avatar" role="img" aria-label="Reviewer portrait"></div><div class="reviewer">Leo Marsh, Valued Client</div><div class="stars"><span></span><span></span><span></span><span></span><span></span></div></div>
<div class="review-foot abs" style="left:773px"><div class="avatar" role="img" aria-label="Reviewer portrait"></div><div class="reviewer">Leo Marsh, Valued Client</div><div class="stars"><span></span><span></span><span></span><span></span><span></span></div></div>

<section class="reserve abs" role="img" aria-label="Warm amber backdrop of hands toasting with wine glasses"></section>
<h2 class="section-title display abs reserve-title" style="font-size:42px">RESERVATIONS</h2>
<p class="reserve-copy abs">Reservations for Corvina Bistro Cabo San Lucas open 7 days. For reservations less than 48 hours in advance, please call us at our local Mexico number: 624 555 0142</p>
<form class="form abs">
  <div class="field"><label>Date</label><div class="input"></div></div>
  <div class="field"><label>Time</label><div class="input"></div></div>
  <div class="field"><label>Party Size</label><div class="input"></div></div>
  <div class="field"><label>Name</label><div class="input"></div></div>
  <div class="field"><label>Email</label><div class="input"></div></div>
  <div class="field"><label>Phone Number (Optional)</label><div class="input"></div></div>
  <div class="field"><label>Hotel Name</label><div class="input"></div></div>
  <div class="field"><label>Room Number</label><div class="input"></div></div>
  <div class="field"><label>Guest Email</label><div class="input"></div></div>
  <div class="field wide"><label>Comments (Optional)</label><div class="input"></div></div>
  <div class="reserve-btn">MAKE A RESERVATION</div>
</form>

<h2 class="contact-title display abs">CONTACT US</h2>
<div class="contact-list abs">
  <div class="contact-item"><span class="ic"><svg width="14" height="18" viewBox="0 0 14 18"><path d="M7 0a7 7 0 0 0-7 7c0 5 7 11 7 11s7-6 7-11a7 7 0 0 0-7-7zm0 9.5A2.5 2.5 0 1 1 7 4.5a2.5 2.5 0 0 1 0 5z" fill="#b4620f"/></svg></span><span>Calle Olivo 12 Centro<br>Cabo San Lucas, Mexico</span></div>
  <div class="contact-item"><span class="ic"><svg width="16" height="16" viewBox="0 0 24 24"><path fill="#b4620f" d="M6.6 10.8a15 15 0 0 0 6.6 6.6l2.2-2.2c.3-.3.7-.4 1-.2 1.1.4 2.3.6 3.6.6.6 0 1 .4 1 1V20c0 .6-.4 1-1 1A17 17 0 0 1 3 4c0-.6.4-1 1-1h3.5c.6 0 1 .4 1 1 0 1.3.2 2.5.6 3.6.1.3 0 .7-.2 1z"/></svg></span><span>CALL US NOW !<br>555 0142</span></div>
  <div class="contact-item"><span class="ic"><svg width="16" height="12" viewBox="0 0 16 12"><rect x="0.5" y="0.5" width="15" height="11" fill="none" stroke="#b4620f"/><path d="M1 1l7 6 7-6" fill="none" stroke="#b4620f"/></svg></span><span>MAIL US<br>hola@corvinabistro.mx</span></div>
</div>
<div class="hours abs">OPEN DAILY FROM 5 TO 12 AM</div>

<div class="tweets abs">
  <div class="tweets-head"><span>TWEETS</span><span>‹ ›</span></div>
  <div class="tweet"><span class="bird"></span><div class="tweet-body"><b>Follow @chirpline Corvina Bistro</b><br>Nemo enim ipsam voluptatem...<br><span class="tweet-date">11 May 2017</span></div></div>
  <div class="tweet"><span class="bird"></span><div class="tweet-body"><b>Follow @chirpline Corvina Bistro</b><br>Nemo enim ipsam voluptatem...<br><span class="tweet-date">11 May 2017</span></div></div>
</div>

<div class="map abs" role="img" aria-label="Street map of downtown Cabo San Lucas with restaurant pin"></div>
<div class="map-card abs">Calle Olivo 12 Centro<br>Cabo San Lucas, Mexico</div>

<div class="footer-line abs"></div>
<div class="socials abs"><span></span><span></span><span></span><span></span></div>
<div class="copyright abs">Copyright © 2017 Corvina Bistro - All Rights Reserved &nbsp;|&nbsp; Terms&amp;conditions &nbsp;|&nbsp; Privacy policy</div>

</body>
</html>
```